Classy, Elegant, Simple Business Card Design

Looking to have a classy, simple, and elegant design. Want a top notch designed business card. I really like the look of the new torvane credit card. I also like the design I attached. I am trying to reach 21-29 year old females for booking us for there wedding or event. We offer Disc Jockey Service, Photo Booth Rentals, and Uplighting .

Target Market(s)

21-28 year old females

Contact Information for Business Card

Has to have logo, website, email, and phone number

Font styles to use
Other font styles liked:
• open to font choice, modern, clean
Designer to choose
33a6d7
0791cd
0555a3
ffffff

Requirements
Must have
• Has to have logo, website, email, and phone number
Nice to have
• I really like the design of the new torvane credit card. I also included my logo and some designs I like
Should not have
• clutter or too much info

```html
<!DOCTYPE html>
<html lang="en">
<head>
<meta charset="utf-8">
<title>Tidelight Event Group – Business Card</title>
<link href="https://fonts.googleapis.com/css2?family=Cinzel:wght@400;500&display=swap" rel="stylesheet">
<style>
  :root {
    --backdrop: #f2f2f2;
    --card: #fdfdfd;
    --silver: #a3a3a3;
    --name-grey: #7a7a7a;
    --ink: #333333;
  }
  * { margin: 0; padding: 0; box-sizing: border-box; }
  html, body {
    width: 1200px;
    height: 900px;
    overflow: hidden;
    background: var(--backdrop);
    font-family: "Cinzel", "Times New Roman", serif;
  }
  .canvas { position: relative; width: 1200px; height: 900px; }
  .card {
    position: absolute;
    left: 288px;
    width: 624px;
    height: 355px;
    background: var(--card);
    text-align: center;
  }
  .card--front { top: 80px; }
  .card--back { top: 465px; }

  .front-mark {
    position: absolute;
    top: 150px;
    left: 0; right: 0;
    font-size: 40px;
    font-weight: 400;
    letter-spacing: 4px;
    color: var(--silver);
  }
  .front-tagline {
    position: absolute;
    top: 300px;
    left: 0; right: 0;
    font-size: 14px;
    letter-spacing: 3.2px;
    color: var(--ink);
  }

  .brand {
    position: absolute;
    top: 66px;
    left: 0; right: 0;
    color: var(--silver);
    font-weight: 400;
  }
  .brand__name { display: block; font-size: 30px; letter-spacing: 1px; line-height: 36px; }
  .brand__sub { display: block; font-size: 13px; letter-spacing: 6px; line-height: 18px; }

  .person {
    position: absolute;
    top: 162px;
    left: 0; right: 0;
    font-size: 21px;
    letter-spacing: 1.5px;
    color: var(--name-grey);
    font-weight: 500;
  }
  .contact {
    position: absolute;
    top: 216px;
    left: 0; right: 0;
    list-style: none;
    font-size: 15px;
    line-height: 27px;
    color: var(--ink);
  }
</style>
</head>
<body>
<main class="canvas">
  <section class="card card--front">
    <div class="front-mark">TIDELIGHT</div>
    <p class="front-tagline">TIDELIGHTEVENTGROUP</p>
  </section>

  <section class="card card--back">
    <div class="brand">
      <span class="brand__name">TIDELIGHT</span>
      <span class="brand__sub">EVENT GROUP</span>
    </div>
    <h1 class="person">DANIEL M. CARTER</h1>
    <ul class="contact">
      <li class="contact__phone">555 014 2290</li>
      <li class="contact__email">HELLO@TIDELIGHTEVENTGROUP.COM</li>
      <li class="contact__web">WWW.TIDELIGHTEVENTGROUP.COM</li>
    </ul>
  </section>
</main>
</body>
</html>
```